VOMRA Pty Ltd Business Card

Looking for a simple yet eye-catching double-sided business card design using my company logo on one side and contact details on the other.

Target Market(s)

Government

Industry/Entity Type

Communication Systems Engineering

Contact Information for Business Card

VOMRA Pty Ltd

Requirements
Nice to have
• Would be great to have a QR code so details can be scanned into contacts

```html
<!DOCTYPE html>
<html lang="en">
<head>
<meta charset="UTF-8">
<title>VOMRA Pty Ltd Business Card</title>
<link href="https://fonts.googleapis.com/css2?family=Open+Sans:wght@400;700&display=swap" rel="stylesheet">
<style>
  :root {
    --backdrop: #222222;
    --card: #37424a;
    --ink-light: #ffffff;
    --ink-dark: #1c1f22;
    --band: #ffffff;
    --rule: #9aa3a9;
  }
  * { margin: 0; padding: 0; box-sizing: border-box; }
  html, body {
    width: 1200px; height: 780px; overflow: hidden;
    background: var(--backdrop);
    font-family: "Open Sans", Arial, sans-serif;
  }
  .sheet {
    width: 1200px; height: 780px;
    display: flex; align-items: center; justify-content: center; gap: 40px;
  }
  .card {
    position: relative;
    width: 540px; height: 310px;
    background: var(--card);
    color: var(--ink-light);
    overflow: hidden;
  }
  .brand {
    position: absolute;
    display: flex; align-items: center; gap: 18px;
  }
  .brand-dot {
    border: 2px solid var(--ink-light);
    border-radius: 50%;
  }
  .brand-name {
    font-weight: 700; letter-spacing: 3px; line-height: 1;
  }
  .card-front .brand { left: 50%; top: 50%; transform: translate(-50%, -50%); }
  .card-front .brand-dot { width: 84px; height: 84px; }
  .card-front .brand-name { font-size: 64px; }

  .card-back .brand { left: 50%; top: 30px; transform: translateX(-50%); }
  .card-back .brand-dot { width: 62px; height: 62px; }
  .card-back .brand-name { font-size: 46px; }

  .holder {
    position: absolute; right: 300px; top: 160px; text-align: right;
  }
  .holder-name { font-size: 25px; font-weight: 700; line-height: 1.1; }
  .holder-role { font-size: 15px; font-weight: 400; }
  .divider {
    position: absolute; left: 262px; top: 132px;
    width: 1px; height: 96px; background: var(--rule);
  }
  .contacts {
    position: absolute; left: 286px; top: 138px;
    list-style: none; font-size: 14.5px; line-height: 1;
  }
  .contacts li { display: flex; align-items: center; gap: 9px; margin-bottom: 11px; }
  .contacts svg { width: 14px; height: 14px; flex: none; }
  .address-band {
    position: absolute; left: 0; right: 0; bottom: 34px; height: 30px;
    background: var(--band); color: var(--ink-dark);
    font-size: 15px; display: flex; align-items: center; justify-content: center;
  }
</style>
</head>
<body>
<main class="sheet">
  <section class="card card-front" aria-label="Business card front">
    <div class="brand">
      <span class="brand-dot"></span>
      <span class="brand-name">VOMRA</span>
    </div>
  </section>

  <section class="card card-back" aria-label="Business card back">
    <div class="brand">
      <span class="brand-dot"></span>
      <span class="brand-name">VOMRA</span>
    </div>

    <div class="holder">
      <p class="holder-name">Jordan Hale</p>
      <p class="holder-role">Co-Founder</p>
    </div>

    <span class="divider"></span>

    <ul class="contacts">
      <li>
        <svg viewBox="0 0 24 24" aria-hidden="true"><path fill="#fff" d="M6.6 10.8a15 15 0 0 0 6.6 6.6l2.2-2.2c.3-.3.7-.4 1-.2 1.1.4 2.3.6 3.6.6.6 0 1 .4 1 1V20c0 .6-.4 1-1 1A17 17 0 0 1 3 4c0-.6.4-1 1-1h3.5c.6 0 1 .4 1 1 0 1.3.2 2.5.6 3.6.1.3 0 .7-.2 1z"/></svg>
        <span>(555) 410-2286</span>
      </li>
      <li>
        <svg viewBox="0 0 24 24" aria-hidden="true"><circle cx="12" cy="12" r="9" fill="none" stroke="#fff" stroke-width="2"/><path d="M3 12h18M12 3c3 3 3 15 0 18M12 3c-3 3-3 15 0 18" fill="none" stroke="#fff" stroke-width="1.6"/></svg>
        <span>www.vomra.com.au</span>
      </li>
      <li>
        <svg viewBox="0 0 24 24" aria-hidden="true"><rect x="2" y="5" width="20" height="14" rx="1.5" fill="none" stroke="#fff" stroke-width="2"/><path d="M2.5 6l9.5 7 9.5-7" fill="none" stroke="#fff" stroke-width="2"/></svg>
        <span>admin@vomra.com.au</span>
      </li>
    </ul>

    <p class="address-band">42-44 Harlow Street Ridgefield NSW 2099 Australia</p>
  </section>
</main>
</body>
</html>
```